NZ First of it's kind solutions directory and marketplace for busy Mums needs a business card design

We need a business card design for our new nationwide business in NZ (long term plans to go global). We provide solutions to the everyday challenges that busy Mums face by connecting them with quality communities and suppliers of carefully selected, relevant products and services. We sell direct via our online marketplace. The final design should communicate our values of inclusivity, quality and smart solutions. Colours should incorporate our logo colour palette of #477077 and #6ba8b2. Our website is at https://www.brightnestmums.example

Target Market(s)

busy Mums, Age 28 – 50, female, income over $100K, location main centres NZ primarily but NZ wide. Is likely juggling work or career with a young family. Probably had hobbies which have fallen by the wayside.
-Wants to succeed in her chosen career without compromising on family life
-to successfully juggle her career without feeling like she is compromising her children
- Is time poor, something always has to give and it’s generally her health (she’ll stay up late, get stressed)
- probably ex corporate or professional career. Has discretional income

Industry/Entity Type

Business

Contact Information for Business Card

Lena Forbisher, Founder, BrightNestMums.example (Strapline Tap; Gather; Sorted), 47 Kowhai Terrace, Ellerslie, Auckland 1051, New Zealand. Mob: 021 483 517 Ph: +64 (0)9 571 4860

Font styles to use
Other font styles liked:
• Raleway, and/or Architects Daughter

Colors
00a990
33b8a4
86cfc6
cfeae6

Requirements
Must have
• the above details, streamline. the logo and colours associated with those logos
Should not have
• foil or metallic colours

```html
<!DOCTYPE html>
<html lang="en">
<head>
<meta charset="utf-8">
<title>BrightNestMums business card</title>
<link rel="stylesheet" href="https://fonts.googleapis.com/css2?family=Raleway:wght@400;500;700;800&display=swap">
<style>
  :root {
    --bg: #2b2b2b;
    --card: #ffffff;
    --teal-dark: #477077;
    --teal-light: #6ba8b2;
    --ink: #3b4a4d;
    --rule: #9cc5cb;
  }
  * { box-sizing: border-box; margin: 0; padding: 0; }
  html, body { width: 1200px; height: 880px; overflow: hidden; }
  body {
    background: var(--bg);
    font-family: "Raleway", sans-serif;
    position: relative;
  }
  .card {
    position: absolute;
    width: 620px;
    height: 354px;
    background: var(--card);
    border-radius: 18px;
    overflow: hidden;
    box-shadow: 0 12px 30px rgba(0,0,0,.45);
  }
  .card--front { left: 110px; top: 60px; }
  .card--back  { left: 470px; top: 462px; }

  .brand {
    display: flex;
    align-items: center;
    gap: 14px;
  }
  .brand__dot {
    width: 44px; height: 44px;
    border-radius: 50%;
    background: var(--teal-dark);
    flex: none;
  }
  .brand__name {
    font-weight: 800;
    color: var(--teal-dark);
    letter-spacing: -0.5px;
  }

  /* front */
  .front__inner {
    position: absolute; inset: 0;
    display: flex; flex-direction: column;
    align-items: center; justify-content: center;
    gap: 14px;
  }
  .front__inner .brand__name { font-size: 44px; }
  .front__url {
    font-size: 15px;
    letter-spacing: 2px;
    color: var(--teal-dark);
    font-weight: 500;
  }

  /* back */
  .back__brand {
    position: absolute; left: 60px; top: 54px;
  }
  .back__brand .brand__dot { width: 48px; height: 48px; }
  .back__brand .brand__name { font-size: 46px; }
  .person {
    position: absolute; left: 0; right: 0; top: 128px;
    text-align: center;
  }
  .person__name { font-size: 20px; font-weight: 700; color: var(--teal-dark); }
  .person__name span { color: var(--teal-light); }
  .person__role { font-size: 15px; color: var(--ink); margin-top: 2px; }

  .details {
    position: absolute; left: 0; right: 0; top: 196px;
    display: flex; justify-content: center; align-items: stretch;
    gap: 24px;
  }
  .address {
    text-align: right;
    font-size: 15px; line-height: 1.5; color: var(--ink);
  }
  .divider { width: 1px; background: var(--rule); }
  .contacts { list-style: none; font-size: 15px; line-height: 1.5; color: var(--ink); }
  .contacts li { display: flex; align-items: center; gap: 8px; }
  .contacts svg { width: 15px; height: 15px; flex: none; }

  .band {
    position: absolute; left: 0; right: 0; bottom: 0; height: 16px;
    background: linear-gradient(100deg, var(--teal-dark) 0 48%, var(--teal-light) 48% 100%);
  }
</style>
</head>
<body>

<section class="card card--front" aria-label="Business card front">
  <div class="front__inner">
    <div class="brand">
      <span class="brand__dot"></span>
      <span class="brand__name">BrightNestMums</span>
    </div>
    <p class="front__url">www.brightnestmums.example</p>
  </div>
</section>

<section class="card card--back" aria-label="Business card back">
  <div class="brand back__brand">
    <span class="brand__dot"></span>
    <span class="brand__name">BrightNestMums</span>
  </div>

  <div class="person">
    <p class="person__name">Lena <span>Forbisher</span></p>
    <p class="person__role">Founder</p>
  </div>

  <div class="details">
    <address class="address" style="font-style:normal">
      47 Kowhai Terrace<br>
      Ellerslie, Auckland 1051<br>
      New Zealand
    </address>
    <span class="divider"></span>
    <ul class="contacts">
      <li>
        <svg viewBox="0 0 16 16" fill="none" stroke="#477077" stroke-width="1.3"><circle cx="8" cy="8" r="7"/><rect x="5.5" y="3.5" width="5" height="9" rx="1"/></svg>
        021 483 517
      </li>
      <li>
        <svg viewBox="0 0 16 16" fill="none" stroke="#477077" stroke-width="1.3"><circle cx="8" cy="8" r="7"/><path d="M5 6.5c0-1 1-1.5 3-1.5s3 .5 3 1.5M5.5 7.5h5l.5 3h-6z"/></svg>
        +64 (0)9 571 4860
      </li>
      <li>
        <svg viewBox="0 0 16 16" fill="none" stroke="#477077" stroke-width="1.3"><circle cx="8" cy="8" r="7"/><ellipse cx="8" cy="8" rx="3" ry="5"/><path d="M3.5 8h9"/></svg>
        www.brightnestmums.example
      </li>
    </ul>
  </div>

  <div class="band"></div>
</section>

</body>
</html>
```